Photography business - business card design quick turn around

Create a business card design for me please. I actually need the final design back before the end of Sunday 13th May 7pm GMT. Sorry for the short notice.

Photoshop artwork template uploaded with artwork guidelines including printer profiles and other mandatory specifications. Only one side of the business card is required as the other side will be an image.

The design is required as an unflattened PSD file so that I can edit the text if I need to.

My brand colours are white and the teal you see in the logo. Occasionally I also use a dark grey on my website (I don't mind the shade of grey as appreciate grey on teal would be a different grey, to the grey I use on white on the website, so just use a shade of grey that matches). Font can be as the font for the logo or if you prefer I am open to another sans serif, easily legible font. Ideally font size will be 12+.Please do not use capital letters for text. I prefer everything to be lower case, if possible.

Thank you.

Lena

Target Market(s)

Other business owners who may refer me and families

Industry/Entity Type

Photographer

Contact Information for Business Card

Silver Kettle Photography Logo
Sub text: family portraiture, captured with love

Contact information, ideally using simple icons to represent email / website / facebook / instagram / pinterest

email: lena@silverkettlephotography.co.uk
website: silverkettlephotography.co.uk
facebook: @silverkettlephotography
pinterest: pinboardly.com/silverkettlepho
instagram: @silverkettle_photography
mobile/telephone: 07713460291

If there is too much text then please drop the instagram and pinterest information.

Font styles to use
Sans Serif

Colors
33b8a4

Requirements
Must have
• Logo
• Contact details as listed above
• sub text
Nice to have
• Instagram and Pinterest contact details
• Nice to have icons to represent website / phone / facebook etc followered by the handle where relevant

```html
<!DOCTYPE html>
<html lang="en">
<head>
<meta charset="utf-8">
<title>Silver Kettle Photography – business card</title>
<link rel="stylesheet" href="https://fonts.googleapis.com/css2?family=Questrial&family=Great+Vibes&display=swap">
<style>
  :root {
    --backdrop: #1c1c1c;
    --card-white: #f4f4f4;
    --teal: #33b8a4;
    --charcoal: #333335;
    --light-text: #e2e2e2;
    --ink: #2b2b2b;
  }
  * { box-sizing: border-box; margin: 0; padding: 0; }
  html, body {
    width: 1200px;
    height: 873px;
    overflow: hidden;
    background: var(--backdrop);
  }
  .canvas {
    position: relative;
    width: 1200px;
    height: 873px;
  }
  .card {
    position: absolute;
    left: 100px;
    top: 151px;
    width: 1000px;
    height: 571px;
    background: linear-gradient(160deg, #ffffff 0%, var(--card-white) 60%, #e6e6e6 100%);
    overflow: hidden;
    font-family: "Questrial", "Century Gothic", sans-serif;
  }
  .card__waves {
    position: absolute;
    inset: 0;
    width: 100%;
    height: 100%;
  }
  .wave--teal { fill: var(--teal); }
  .wave--dark { fill: var(--charcoal); }

  .brand {
    position: absolute;
    left: 150px;
    top: 78px;
    display: flex;
    align-items: center;
    gap: 18px;
  }
  .brand__dot {
    width: 46px;
    height: 46px;
    border-radius: 50%;
    background: var(--teal);
  }
  .brand__name {
    color: var(--teal);
    font-size: 40px;
    line-height: 1;
    letter-spacing: 0.5px;
  }

  .tagline {
    position: absolute;
    left: 120px;
    top: 160px;
    width: 560px;
    display: flex;
    align-items: center;
    gap: 16px;
  }
  .tagline__rule {
    flex: 1;
    height: 2px;
    background: var(--teal);
  }
  .tagline__text {
    font-family: "Great Vibes", cursive;
    font-size: 34px;
    color: var(--ink);
    white-space: nowrap;
  }

  .contacts {
    position: absolute;
    list-style: none;
    color: var(--light-text);
    font-size: 22px;
  }
  .contacts li {
    display: flex;
    align-items: center;
    gap: 16px;
    height: 42px;
    white-space: nowrap;
  }
  .contacts--primary { left: 70px; top: 400px; }
  .contacts--social { left: 600px; top: 304px; }

  .icon {
    width: 24px;
    height: 24px;
    flex: none;
    fill: var(--teal);
  }
  .icon--social {
    width: 18px;
    height: 18px;
    border-radius: 50%;
    background: var(--teal);
    margin: 0 3px;
  }
</style>
</head>
<body>
<main class="canvas">
  <section class="card" aria-label="Silver Kettle Photography business card">
    <svg class="card__waves" viewBox="0 0 1000 571" preserveAspectRatio="none" aria-hidden="true">
      <path class="wave--teal" d="M0,318 C240,272 600,318 1000,150 L1000,571 L0,571 Z"/>
      <path class="wave--dark" d="M0,338 C260,300 620,336 1000,182 L1000,571 L0,571 Z"/>
    </svg>

    <div class="brand">
      <span class="brand__dot" aria-hidden="true"></span>
      <span class="brand__name">silver kettle photography</span>
    </div>

    <div class="tagline">
      <span class="tagline__rule"></span>
      <span class="tagline__text">Family Portraiture, Captured with Love</span>
      <span class="tagline__rule"></span>
    </div>

    <ul class="contacts contacts--social">
      <li><span class="icon icon--social" aria-hidden="true"></span>@silverkettlephotography</li>
      <li><span class="icon icon--social" aria-hidden="true"></span>pinboardly.com/silverkettlepho</li>
      <li><span class="icon icon--social" aria-hidden="true"></span>@silverkettle_photography</li>
    </ul>

    <ul class="contacts contacts--primary">
      <li>
        <svg class="icon" viewBox="0 0 24 24" aria-hidden="true">
          <path d="M6.6 10.8a15.1 15.1 0 0 0 6.6 6.6l2.2-2.2a1 1 0 0 1 1-.25 11.4 11.4 0 0 0 3.6.57 1 1 0 0 1 1 1V20a1 1 0 0 1-1 1A17 17 0 0 1 3 4a1 1 0 0 1 1-1h3.5a1 1 0 0 1 1 1c0 1.25.2 2.45.57 3.57a1 1 0 0 1-.25 1z"/>
        </svg>
        07713460291
      </li>
      <li>
        <svg class="icon" viewBox="0 0 24 24" aria-hidden="true">
          <path d="M2 5h20v14H2zm2 2v.3l8 5.6 8-5.6V7zm16 2.7-8 5.6-8-5.6V17h16z" fill-rule="evenodd"/>
        </svg>
        lena@silverkettlephotography.co.uk
      </li>
      <li>
        <svg class="icon" viewBox="0 0 24 24" aria-hidden="true">
          <path d="M10.6 13.4a1 1 0 0 1 0-1.4l4-4a1 1 0 1 1 1.4 1.4l-4 4a1 1 0 0 1-1.4 0zM8.5 19.5a4.2 4.2 0 0 1-3-7.2l2.8-2.8 1.4 1.4-2.8 2.8a2.2 2.2 0 0 0 3.1 3.1l2.8-2.8 1.4 1.4-2.8 2.8a4.2 4.2 0 0 1-2.9 1.3zm7.6-5.5-1.4-1.4 2.8-2.8a2.2 2.2 0 0 0-3.1-3.1l-2.8 2.8-1.4-1.4 2.8-2.8a4.2 4.2 0 0 1 5.9 5.9z"/>
        </svg>
        www.silverkettlephotography.co.uk
      </li>
    </ul>
  </section>
</main>
</body>
</html>
```